Real Estate Development requires a tri-fold corporate brochure

I need a clean, elegant, Corporate tri-fold brochure for a real estate development. Currently operation in Dubai, we plan to enter European markets and will hand out the brochures to potential, future cooperation partners. A color combination in line with our logo would be great. The overall design should communicate that we are holding numerous high-end properties in Dubai and London and our financial strength.

Target Market(s)

Europe

Industry/Entity Type

Real Estate Development

Contact Information for Business Card

Lorin Vasquel, MBA
Senior Business Development Manager
Marble Crest UAE
Cell UAE: +971 56 482 9153
Cell Austria: +43 650 317 8826
lova@marblecrest.ae

Requirements
Must have
• Clean, corporate design, not too colorful, a few nice pictures of existing real estate properties. See the attached pdf-document for more details.
Nice to have
• Refurbished logo

```html
<!DOCTYPE html>
<html lang="en">
<head>
<meta charset="utf-8">
<title>Tri-Fold Brochure – Back Spread</title>
<link href="https://fonts.googleapis.com/css2?family=Libre+Baskerville:wght@400;700&family=Open+Sans:wght@400&display=swap" rel="stylesheet">
<style>
  :root{
    --page-bg:#bcc2c9;
    --navy-deep:#0b2468;
    --navy:#123a8c;
    --sky:#2a6cb8;
    --dusk:#3a5f86;
    --night:#13202e;
    --accent-yellow:#d6dc2a;
    --panel-yellow:rgba(200,216,40,.93);
    --text-light:#ffffff;
    --text-dark:#1b2a3e;
    --label-dark:#0f2340;
    --rule:rgba(150,170,220,.7);
  }
  html,body{margin:0;padding:0;width:1200px;height:900px;overflow:hidden;background:var(--page-bg);}
  .spread{
    position:absolute;left:20px;top:72px;
    width:1257px;height:818px;
    transform:scale(.92284);transform-origin:0 0;
    overflow:hidden;
    background:var(--navy-deep);
  }
  .skyline-photo{
    position:absolute;inset:0;
    background:
      radial-gradient(ellipse 60% 30% at 62% 82%, rgba(200,130,70,.55), transparent 70%),
      radial-gradient(ellipse 40% 25% at 95% 62%, rgba(230,160,110,.35), transparent 70%),
      linear-gradient(180deg, var(--navy-deep) 0%, var(--navy) 25%, var(--sky) 52%, var(--dusk) 66%, var(--night) 88%, #0d1620 100%);
  }
  .fold{position:absolute;top:0;bottom:0;width:2px;background:linear-gradient(90deg,rgba(0,0,0,.12),rgba(255,255,255,.06));}
  .fold--one{left:419px}
  .fold--two{left:838px}
  .wheel{position:absolute;left:0;top:0;width:1257px;height:818px}
  .headline{
    position:absolute;margin:0;
    font-family:"Libre Baskerville",Georgia,serif;font-weight:700;
    font-size:38px;letter-spacing:5.8px;color:var(--accent-yellow);
    white-space:nowrap;line-height:1;
  }
  .headline--top{left:226px;top:56px}
  .headline--bottom{left:420px;top:117px}
  .headline-rule{position:absolute;height:2px;background:var(--rule)}
  .headline-rule--top{left:198px;width:750px;top:100px}
  .headline-rule--bottom{left:404px;width:853px;top:162px}
  .sector-label{
    position:absolute;transform:translate(-50%,-50%);
    font-family:"Libre Baskerville",Georgia,serif;font-size:14px;color:var(--label-dark);
    letter-spacing:.5px;white-space:nowrap;
  }
  .statement{
    position:absolute;left:922px;top:208px;margin:0;
    font-family:"Libre Baskerville",Georgia,serif;font-size:12.4px;line-height:22.2px;
    color:var(--text-light);
  }
  .statement span{display:block;white-space:nowrap}
  .quote-mark{
    position:absolute;font-family:"Libre Baskerville",Georgia,serif;font-weight:700;
    font-size:70px;line-height:1;color:var(--accent-yellow);
  }
  .quote-mark--open{left:882px;top:186px}
  .quote-mark--close{left:1056px;top:344px}
  .intro-copy{
    position:absolute;left:67px;top:577px;width:236px;margin:0;
    font-family:"Open Sans",Arial,sans-serif;font-size:8.3px;line-height:15.9px;
    color:var(--text-light);
  }
  .value-panel{
    position:absolute;left:838px;top:631px;width:419px;height:132px;
    background:var(--panel-yellow);
  }
  .value-panel p{
    margin:0;position:absolute;left:68px;top:19px;width:284px;
    font-family:"Open Sans",Arial,sans-serif;font-size:8.6px;line-height:18px;
    color:var(--text-dark);text-align:justify;
  }
</style>
</head>
<body>
  <div class="spread">
    <div class="skyline-photo" role="img" aria-label="Photo: city skyline at dusk with a supertall tower, illuminated high-rises and light trails on highways"></div>
    <div class="fold fold--one"></div>
    <div class="fold fold--two"></div>

    <svg class="wheel" viewBox="0 0 1257 818">
      <defs>
        <linearGradient id="hospitality-fill" x1="0" y1="0" x2="1" y2="1">
          <stop offset="0" stop-color="#6d5aa8"/><stop offset=".5" stop-color="#c9b7e0"/><stop offset="1" stop-color="#3c4f8e"/>
        </linearGradient>
        <linearGradient id="leisure-fill" x1="0" y1="0" x2="0" y2="1">
          <stop offset="0" stop-color="#7fa8d6"/><stop offset=".55" stop-color="#d9c8b0"/><stop offset="1" stop-color="#2f8fb8"/>
        </linearGradient>
        <linearGradient id="residential-fill" x1="0" y1="0" x2="1" y2="1">
          <stop offset="0" stop-color="#a9c6ea"/><stop offset=".5" stop-color="#e8d9a8"/><stop offset="1" stop-color="#6b7a86"/>
        </linearGradient>
        <linearGradient id="commercial-fill" x1="0" y1="0" x2="1" y2="1">
          <stop offset="0" stop-color="#d7dbe6"/><stop offset=".5" stop-color="#4a5a78"/><stop offset="1" stop-color="#1b2438"/>
        </linearGradient>
        <linearGradient id="highrise-fill" x1="0" y1="0" x2="0" y2="1">
          <stop offset="0" stop-color="#1e4f96"/><stop offset="1" stop-color="#142236"/>
        </linearGradient>
        <radialGradient id="bubble" cx=".5" cy=".5" r=".5">
          <stop offset="0" stop-color="#ffffff"/><stop offset=".55" stop-color="#e3f2fb" stop-opacity=".95"/><stop offset="1" stop-color="#8cc8ea" stop-opacity=".55"/>
        </radialGradient>
      </defs>

      <path role="img" aria-label="Photo: high-rise towers at night" fill="url(#highrise-fill)" opacity=".55"
        d="M -50 300 A 560 560 0 0 1 510 860 L -50 860 Z"/>

      <path role="img" aria-label="Photo: sail-shaped luxury hotel tower against a purple sky" fill="url(#hospitality-fill)"
        d="M -50 116 A 744 744 0 0 1 252.6 180.4 L 177.8 348.4 A 560 560 0 0 0 -50 300 Z"/>
      <path role="img" aria-label="Photo: resort hotel with palm trees and pool" fill="url(#leisure-fill)"
        d="M 252.6 180.4 A 744 744 0 0 1 479.7 337.6 L 348.7 466.8 A 560 560 0 0 0 177.8 348.4 Z"/>
      <path role="img" aria-label="Photo: modern residential apartment building with balconies" fill="url(#residential-fill)"
        d="M 479.7 337.6 A 744 744 0 0 1 627 551.5 L 459.6 627.8 A 560 560 0 0 0 348.7 466.8 Z"/>
      <path role="img" aria-label="Photo: glass office building lit at dusk" fill="url(#commercial-fill)"
        d="M 627 551.5 A 744 744 0 0 1 694 860 L 510 860 A 560 560 0 0 0 459.6 627.8 Z"/>

      <g fill="none" stroke="#ffffff" stroke-opacity=".85" stroke-width="2">
        <line x1="252.6" y1="180.4" x2="177.8" y2="348.4"/>
        <line x1="479.7" y1="337.6" x2="348.7" y2="466.8"/>
        <line x1="627" y1="551.5" x2="459.6" y2="627.8"/>
      </g>
      <path d="M -50 116 A 744 744 0 0 1 694 860" fill="none" stroke="#3fa3e8" stroke-opacity=".5" stroke-width="18"/>
      <path d="M -50 116 A 744 744 0 0 1 694 860" fill="none" stroke="#dff1ff" stroke-width="2.5"/>
      <path d="M -50 300 A 560 560 0 0 1 510 860" fill="none" stroke="#bfe3ff" stroke-opacity=".8" stroke-width="1.5"/>

      <circle cx="70" cy="149" r="52" fill="url(#bubble)"/>
      <circle cx="318" cy="394" r="52" fill="url(#bubble)"/>
      <circle cx="556" cy="406" r="54" fill="url(#bubble)"/>
      <circle cx="498" cy="726" r="52" fill="url(#bubble)"/>
    </svg>

    <span class="sector-label" style="left:70px;top:151px">Hospitality</span>
    <span class="sector-label" style="left:318px;top:391px">Leisure</span>
    <span class="sector-label" style="left:557px;top:404px">Residential</span>
    <span class="sector-label" style="left:500px;top:717px">Commercial</span>

    <h1 class="headline headline--top">EXPAND YOUR WORLD OF</h1>
    <div class="headline-rule headline-rule--top"></div>
    <h1 class="headline headline--bottom">INVESTMENT CHOICES</h1>
    <div class="headline-rule headline-rule--bottom"></div>

    <span class="quote-mark quote-mark--open">“</span>
    <p class="statement">
      <span>We are currently exploring possible</span>
      <span>opportunities and cooperation in</span>
      <span>context with our plans of further</span>
      <span>diversifying our real-estate portfolio</span>
      <span>i.e. the intention to further invest in</span>
      <span>opportunities in European Union</span>
      <span>Member Countries.</span>
    </p>
    <span class="quote-mark quote-mark--close">”</span>

    <p class="intro-copy">Our target properties span a broad range of investments, including hospitality, leisure, residential and commercial. This includes both “off-Plan” properties and completed properties. Additionally, we seek underperforming and distressed properties where we can add value through renovation, repositioning, redeployment, or expansion. We focus on mid and long term real estate investment opportunities with a potential for above average capital gain and solid rental income.</p>

    <div class="value-panel">
      <p>By identifying opportunities and adding real value, we have consistently produced industry-leading returns across all asset classes. The end goal is to capitalize on market inefficiencies, creating value through strategic acquisitions, effective management and well-timed divestitures.</p>
    </div>
  </div>
</body>
</html>
```